Electronic Letterhead for The Harborline Partners, LLC

I would like to have an electronic letterhead layout using Word for first and second page letterhead using my previously designed logo. The logo was successfully designed by a designer for the Pixel Bazaar. I would like to only use the "C" portion of the logo on the second page. I would like the designer that designed my logo to be included in the designers that participate in this competition.

Target Market(s)

My clients are typically governmental entities or financial entities

Industry/Entity Type

Electronic

Font styles to use
Sans Serif

Requirements
Must have
• Utilize existing logo
Nice to have
• Fist and second page letterhead design in electronic format (Word)

```html
<!DOCTYPE html>
<html lang="en">
<head>
<meta charset="utf-8">
<title>The Harborline Partners, LLC — Letterhead</title>
<link rel="stylesheet" href="https://fonts.googleapis.com/css2?family=Questrial&display=swap">
<style>
  :root {
    --backdrop: #e9e9ea;
    --paper: #fbfbfb;
    --brand-blue: #26488a;
    --bar-grey: #77777a;
    --text-grey: #55565a;
    --ink: #333438;
  }
  * { margin: 0; padding: 0; box-sizing: border-box; }
  html, body {
    width: 1200px;
    height: 936px;
    overflow: hidden;
    background: var(--backdrop);
    font-family: "Questrial", "Century Gothic", sans-serif;
  }
  .canvas {
    width: 1200px;
    height: 936px;
    display: flex;
    align-items: center;
    justify-content: center;
  }
  .letterhead {
    position: relative;
    width: 610px;
    height: 862px;
    background: var(--paper);
    box-shadow: 0 2px 10px rgba(0, 0, 0, 0.08);
  }
  .brand {
    position: absolute;
    top: 58px;
    left: 64px;
    display: flex;
    align-items: center;
    gap: 12px;
  }
  .brand-dot {
    width: 30px;
    height: 30px;
    border-radius: 50%;
    background: var(--brand-blue);
  }
  .brand-name {
    color: var(--brand-blue);
    font-size: 17px;
    letter-spacing: 0.06em;
    text-transform: uppercase;
    line-height: 1.2;
  }
  .edge-mark {
    position: absolute;
    left: 0;
    top: 300px;
    width: 8px;
    height: 44px;
    background: var(--brand-blue);
  }
  .footer-bar {
    position: absolute;
    right: 0;
    bottom: 92px;
    width: 8px;
    height: 112px;
    background: var(--bar-grey);
  }
  .website {
    position: absolute;
    left: 64px;
    bottom: 44px;
    font-size: 10px;
    letter-spacing: 0.32em;
    color: var(--text-grey);
  }
  .website strong {
    font-weight: 400;
    color: var(--brand-blue);
  }
  .contact {
    position: absolute;
    right: 34px;
    bottom: 100px;
    font-size: 9.5px;
    color: var(--ink);
    line-height: 1.7;
    text-align: left;
  }
  .contact-line {
    display: flex;
    align-items: center;
    gap: 5px;
  }
  .contact-item {
    display: inline-flex;
    align-items: center;
    gap: 4px;
    margin-right: 6px;
  }
  .contact-icon {
    width: 10px;
    height: 10px;
  }
</style>
</head>
<body>
  <main class="canvas">
    <article class="letterhead">
      <header class="brand">
        <span class="brand-dot" aria-hidden="true"></span>
        <span class="brand-name">The Harborline Partners, LLC</span>
      </header>

      <span class="edge-mark" aria-hidden="true"></span>

      <footer>
        <address class="contact">
          <div class="contact-line">1185 Lanier Ave #4 Austin, TX 78701</div>
          <div class="contact-line">
            <span class="contact-item">
              <svg class="contact-icon" viewBox="0 0 10 10" aria-hidden="true">
                <circle cx="5" cy="5" r="4.6" fill="none" stroke="#26488a" stroke-width="0.8"/>
                <path d="M3.4 2.8 L4.3 3.9 L3.9 4.4 Q4.5 5.6 5.6 6.1 L6.1 5.7 L7.2 6.6 L6.6 7.3 Q4.4 7.1 2.7 3.4 Z" fill="#26488a"/>
              </svg>
              +1 512 555 0148
            </span>
            <span class="contact-item">
              <svg class="contact-icon" viewBox="0 0 10 10" aria-hidden="true">
                <circle cx="5" cy="5" r="4.6" fill="none" stroke="#26488a" stroke-width="0.8"/>
                <rect x="2.7" y="3.4" width="4.6" height="3.2" fill="none" stroke="#26488a" stroke-width="0.7"/>
                <path d="M2.7 3.4 L5 5.2 L7.3 3.4" fill="none" stroke="#26488a" stroke-width="0.7"/>
              </svg>
              info@harborlinepartners.com
            </span>
          </div>
        </address>
        <span class="footer-bar" aria-hidden="true"></span>
        <p class="website">www.<strong>harborlinepartners</strong>.com</p>
      </footer>
    </article>
  </main>
</body>
</html>
```